Design and Renovation Company Luxury Business Card

I want to create a luxury business card for a Design and Renovation Firm . We will use our current logo. The company name is 528BUILDA. We do not want anything standard. We need a very unique concept.
Please see uploaded inspiration. I really like the textured paper option. I would like the card to be thick with debossing, and/or embossing options. The logo has orange in it but I would like to see the card with and without the orange. I think the orange may make the company feel less high-end. The goal is to elevate the logo not match its vibe per se of the logo. We want something very unique, not standard at all!
I would like a space for :
Logo,
Name,
Position,
Email,
Office number,
Website Address,
Business Address,
Thank you!
Have fun!
Target Market(s)
Home owners Age 35 +
Industry/Entity Type
Design and Renovation
Contact Information for Business Card
Logo, Name, Position, Email, Office number, Website Address, Business Address,.
Colors
Designer to choose colors to be used in the design.
Requirements
Must have
- A luxury designer feel. Must be black or dark grey but open to other luxury ideas.
Nice to have
- Gold, silver, black embossing or debossing. Textured paper design.
Should not have
- A cheap look and feel.

```html
<!DOCTYPE html>
<html lang="en">
<head>
<meta charset="utf-8">
<title>528BUILDA Business Card</title>
<link rel="stylesheet" href="https://fonts.googleapis.com/css2?family=Poppins:wght@300;400;500;600;700&display=swap">
<style>
  :root {
    --backdrop: #d3d7d7;
    --card: #202124;
    --orange: #f39224;
    --white: #ffffff;
    --soft-white: #f2f2f2;
  }
  * { box-sizing: border-box; margin: 0; padding: 0; }
  html, body {
    width: 1200px; height: 960px; overflow: hidden;
    background: var(--backdrop);
    font-family: "Poppins", sans-serif;
  }
  .canvas { position: relative; width: 1200px; height: 960px; }

  .card {
    position: absolute; top: 106px;
    width: 427px; height: 748px;
    background: var(--card);
    border-radius: 26px;
    border-left: 4px solid var(--orange);
    border-bottom: 4px solid var(--orange);
    overflow: hidden;
  }
  .card-front { left: 144px; }
  .card-back { left: 632px; }

  /* front */
  .front-texture {
    position: absolute; inset: 0;
    background:
      radial-gradient(ellipse 70% 55% at 10% 5%, rgba(255,255,255,0.55), rgba(255,255,255,0.12) 55%, rgba(255,255,255,0) 80%),
      linear-gradient(160deg, #2c2d31 0%, #1c1d20 60%, #17181a 100%);
  }
  .front-brand {
    position: absolute;
    left: 165px; top: 512px;
    transform-origin: 0 0;
    transform: rotate(-90deg);
    display: flex; flex-direction: column;
    width: 420px;
  }
  .front-brand .wordmark {
    font-size: 66px; font-weight: 500; color: var(--white);
    letter-spacing: 2px; line-height: 1;
  }
  .front-brand .tagline {
    margin-top: 8px;
    font-size: 16px; font-weight: 500; color: var(--white);
    letter-spacing: 5.2px; line-height: 1;
  }

  /* back */
  .brand-name {
    position: absolute; left: 0; right: 0; top: 210px;
    text-align: center;
    font-size: 36px; font-weight: 500; color: var(--white);
    letter-spacing: 3px;
  }
  .person-name {
    position: absolute; left: 0; right: 0; top: 392px;
    text-align: center; font-size: 35px; line-height: 1.2; color: var(--white);
  }
  .person-name .first { color: var(--orange); font-weight: 700; }
  .person-name .last { font-weight: 300; }
  .person-role {
    position: absolute; left: 0; right: 0; top: 438px;
    text-align: center; font-size: 19px; font-weight: 600; color: var(--soft-white);
  }
  .divider {
    position: absolute; left: 0; right: 0;
    display: flex; align-items: center; justify-content: center; gap: 6px;
  }
  .divider .rule { height: 2px; background: var(--orange); }
  .divider-contact { top: 480px; }
  .divider-contact .rule { width: 54px; }
  .divider-address { top: 629px; }
  .divider-address .rule { width: 116px; }
  .divider svg { display: block; }

  .contact-list {
    position: absolute; left: 0; right: 0; top: 522px;
    list-style: none; text-align: center;
    font-size: 21px; font-weight: 400; color: var(--white);
    line-height: 27.5px; letter-spacing: 0.4px;
  }
  .address {
    position: absolute; left: 0; right: 0; top: 668px;
    text-align: center; font-style: normal;
    font-size: 21px; font-weight: 400; color: var(--white);
    line-height: 27.5px; letter-spacing: 0.4px;
  }
</style>
</head>
<body>
<main class="canvas">

  <section class="card card-front">
    <div class="front-texture" role="img" aria-label="Embossed tile pattern, bright at the upper left fading into the dark card"></div>
    <div class="front-brand">
      <span class="wordmark">528BUILDA</span>
      <span class="tagline">Design and Renovation Firm</span>
    </div>
  </section>

  <section class="card card-back">
    <div class="brand-name">528BUILDA</div>

    <h1 class="person-name"><span class="first">Marketa</span> <span class="last">Dvorska</span></h1>
    <p class="person-role">Founder &amp; CEO</p>

    <div class="divider divider-contact">
      <span class="rule"></span>
      <svg width="34" height="34" viewBox="0 0 34 34" aria-label="Phone">
        <rect x="7" y="7" width="20" height="20" rx="4" transform="rotate(45 17 17)" fill="#f39224"/>
        <path d="M12.5 11.5c.6-.6 1.4-.5 1.8.1l1.2 1.8c.3.5.2 1.1-.2 1.5l-.7.6c.6 1.4 1.6 2.4 3 3l.6-.7c.4-.4 1-.5 1.5-.2l1.8 1.2c.6.4.7 1.2.1 1.8l-.8.8c-.7.7-1.8.9-2.8.4-2.7-1.2-4.9-3.4-6.1-6.1-.5-1-.3-2.1.4-2.8z" fill="#fff"/>
      </svg>
      <svg width="34" height="34" viewBox="0 0 34 34" aria-label="Email">
        <rect x="7" y="7" width="20" height="20" rx="4" transform="rotate(45 17 17)" fill="#f39224"/>
        <rect x="10.5" y="12.5" width="13" height="9" rx="1" fill="none" stroke="#fff" stroke-width="1.5"/>
        <path d="M10.8 13l6.2 4.6 6.2-4.6" fill="none" stroke="#fff" stroke-width="1.5"/>
      </svg>
      <svg width="34" height="34" viewBox="0 0 34 34" aria-label="Website">
        <rect x="7" y="7" width="20" height="20" rx="4" transform="rotate(45 17 17)" fill="#f39224"/>
        <circle cx="17" cy="17" r="6" fill="none" stroke="#fff" stroke-width="1.5"/>
        <path d="M11 17h12M17 11c2 2 2 10 0 12M17 11c-2 2-2 10 0 12" fill="none" stroke="#fff" stroke-width="1.2"/>
      </svg>
      <span class="rule"></span>
    </div>

    <ul class="contact-list">
      <li>(214) 555-0187</li>
      <li>info@yourwebsite.com</li>
      <li>www.yourwebsite.com</li>
    </ul>

    <div class="divider divider-address">
      <span class="rule"></span>
      <svg width="34" height="34" viewBox="0 0 34 34" aria-label="Location">
        <rect x="7" y="7" width="20" height="20" rx="4" transform="rotate(45 17 17)" fill="#f39224"/>
        <path d="M17 23s-4.5-4.6-4.5-8a4.5 4.5 0 0 1 9 0c0 3.4-4.5 8-4.5 8z" fill="none" stroke="#fff" stroke-width="1.5"/>
        <circle cx="17" cy="15" r="1.6" fill="#fff"/>
      </svg>
      <span class="rule"></span>
    </div>

    <address class="address">
      4720 Meadowbrook Rd. Suite 110<br>
      Arlington, TX 76010
    </address>
  </section>

</main>
</body>
</html>
```